Design 4 pages for an event discovery website

This is a contest for the design of 4 pages for an events discovery website. The feature is part of the new sign-up process.

Please see the attached document for a full scope, mockups and the parent category icons.

Target Market(s)

18-35 Australian event goers

Industry/Entity Type

Events

Number of Pages Required

4 page

```html
<!DOCTYPE html>
<html lang="en">
<head>
<meta charset="utf-8">
<title>Linking to Other Accounts</title>
<link href="https://fonts.googleapis.com/css2?family=Titillium+Web:wght@400;600&family=Open+Sans:wght@400&display=swap" rel="stylesheet">
<style>
  :root {
    --brand: #5570c0;
    --ink: #111111;
    --white: #ffffff;
    --field-border: #d6d6d6;
    --footer-bg: #151515;
    --footer-text: #e6e6e6;
    --hero-top: #ebe9ec;
    --hero-mid: #b9bfd0;
    --hero-low: #6f86b8;
    --hero-base: #5a6f9e;
    --chirp-a: #3f93e0;
    --chirp-b: #2e7dcf;
    --snap-a: #22689a;
    --snap-b: #1a5683;
    --tune-a: #94d423;
    --tune-b: #73b316;
    --shelf-a: #3c3c3c;
    --shelf-b: #121212;
    --tick: #7bd12a;
  }
  * { box-sizing: border-box; margin: 0; padding: 0; }
  html, body { width: 1200px; height: 831px; overflow: hidden; }
  body { position: relative; background: var(--white); font-family: "Open Sans", sans-serif; color: var(--ink); }

  .top-rule { position: absolute; left: 0; top: 0; width: 1200px; height: 4px; background: var(--brand); }
  .account-tab { position: absolute; left: 968px; top: 4px; width: 120px; height: 26px; }
  .account-tab svg { position: absolute; inset: 0; }
  .account-tab .links { position: absolute; inset: 0; display: flex; justify-content: center; align-items: center; gap: 8px; font-family: "Titillium Web", sans-serif; font-weight: 600; font-size: 12px; color: var(--white); }
  .account-tab .sep { width: 0; height: 16px; border-left: 1px dotted var(--white); }

  .site-header { position: absolute; left: 0; top: 4px; width: 1200px; height: 120px; border-bottom: 1px solid #cfcfcf; }
  .wordmark { position: absolute; left: 98px; top: 40px; font-family: "Titillium Web", sans-serif; font-weight: 600; font-size: 41px; line-height: 1; color: var(--brand); }
  .main-nav { position: absolute; left: 753px; top: 53px; display: flex; gap: 45px; font-family: "Titillium Web", sans-serif; font-weight: 600; font-size: 16px; }
  .search-field { position: absolute; left: 910px; top: 46px; width: 191px; height: 36px; border: 1px solid var(--field-border); border-radius: 3px; padding-left: 13px; line-height: 34px; font-size: 13px; color: #777; }

  .hero { position: absolute; left: 0; top: 125px; width: 1200px; height: 580px; overflow: hidden; }
  .hero-backdrop { position: absolute; inset: 0;
    background: linear-gradient(180deg, var(--hero-top) 0%, var(--hero-top) 30%, var(--hero-mid) 46%, var(--hero-low) 62%, var(--hero-base) 100%); }
  .hero-title { position: absolute; left: 0; top: 58px; width: 1207px; text-align: center; font-family: "Titillium Web", sans-serif; font-weight: 600; font-size: 53px; line-height: 1; }
  .hero-intro { position: absolute; left: 0; top: 140px; width: 1198px; text-align: center; font-size: 15.5px; line-height: 29px; }

  .account-list { position: absolute; left: 99px; top: 274px; list-style: none; }
  .account-row { position: relative; height: 57px; margin-bottom: 11.5px; width: 900px; }
  .account-button { position: absolute; left: 0; top: 0; width: 206px; height: 57px; border-radius: 3px; display: flex; color: var(--white); font-family: "Titillium Web", sans-serif; font-weight: 600; font-size: 22px; }
  .account-button .badge { width: 64px; border-right: 1px solid rgba(0,0,0,0.18); display: flex; align-items: center; justify-content: center; }
  .account-button .badge span { width: 22px; height: 22px; border-radius: 50%; background: var(--white); }
  .account-button .label { padding-left: 17px; line-height: 57px; }
  .chirp { background: linear-gradient(180deg, var(--chirp-a), var(--chirp-b)); }
  .snap { background: linear-gradient(180deg, var(--snap-a), var(--snap-b)); }
  .tune { background: linear-gradient(180deg, var(--tune-a), var(--tune-b)); }
  .shelf { background: linear-gradient(180deg, var(--shelf-a), var(--shelf-b)); }
  .status { position: absolute; left: 274px; top: 12px; display: flex; align-items: center; gap: 14px; white-space: nowrap; color: var(--white); font-family: "Titillium Web", sans-serif; font-size: 22px; text-shadow: 0 1px 3px rgba(20,30,60,0.45); }

  .site-footer { position: absolute; left: 0; top: 705px; width: 1200px; height: 126px; background: var(--footer-bg); color: var(--footer-text); }
  .footer-nav { position: absolute; left: 98px; top: 36px; font-size: 12.5px; word-spacing: 1px; }
  .copyright { position: absolute; left: 98px; top: 70px; font-size: 12.5px; }
  .social { position: absolute; left: 944px; top: 51px; display: flex; gap: 16px; }
  .social span { width: 27px; height: 27px; }
  .s1 { background: #3b5b9e; } .s2 { background: #1d8fc9; } .s3 { background: #c9c9c9; } .s4 { background: #1a7fbc; }
</style>
</head>
<body>
  <div class="top-rule"></div>
  <header class="site-header">
    <div class="wordmark">VENUELY</div>
    <nav class="main-nav"><span>Find</span><span>Events</span></nav>
    <div class="search-field">Search</div>
  </header>
  <div class="account-tab">
    <svg width="120" height="26" viewBox="0 0 120 26"><path d="M0 0 H120 Q110 4 104 18 Q100 26 92 26 H28 Q20 26 16 18 Q10 4 0 0 Z" fill="#5570c0"/></svg>
    <div class="links"><span>Sign</span><span class="sep"></span><span>Login</span></div>
  </div>

  <section class="hero">
    <div class="hero-backdrop" role="img" aria-label="Soft-focus photo of people enjoying music together"></div>
    <h1 class="hero-title">Linking to Other Accounts</h1>
    <p class="hero-intro">Link in all your other Social Media Account and Music Players<br>by Linking your Account, We can save you a lot of time by automatically your intersts</p>

    <ul class="account-list">
      <li class="account-row">
        <div class="account-button chirp"><div class="badge"><span></span></div><div class="label">Chirpline</div></div>
        <div class="status"><svg width="20" height="16" viewBox="0 0 20 16"><path d="M1 9 L7 14 L19 2" fill="none" stroke="#7bd12a" stroke-width="3"/></svg>Linked</div>
      </li>
      <li class="account-row">
        <div class="account-button snap"><div class="badge"><span></span></div><div class="label">Snapframe</div></div>
      </li>
      <li class="account-row">
        <div class="account-button tune"><div class="badge"><span></span></div><div class="label">Tunewave</div></div>
        <div class="status"><svg width="20" height="16" viewBox="0 0 20 16"><path d="M1 9 L7 14 L19 2" fill="none" stroke="#7bd12a" stroke-width="3"/></svg>We don't have that feature yet but have recarded your interest</div>
      </li>
      <li class="account-row">
        <div class="account-button shelf"><div class="badge"><span></span></div><div class="label">Songshelf</div></div>
      </li>
    </ul>
  </section>

  <footer class="site-footer">
    <nav class="footer-nav">Find &nbsp;/ &nbsp;Events &nbsp;/ &nbsp;About Us &nbsp;/ &nbsp;Search &nbsp;/ &nbsp;Register &nbsp;/ &nbsp;Contact Us</nav>
    <p class="copyright">Copyrights © 2015 Brightgate Studio All Rights Reserved</p>
    <div class="social"><span class="s1"></span><span class="s2"></span><span class="s3"></span><span class="s4"></span></div>
  </footer>
</body>
</html>
```